Sophisticated, clean website reflecting my feminine, playful side to sell my abstract art,

I need a website no more than 3 pages to showcase my paintings, a little about me and some contact info. I do abstracts so looking for something a little edgy, yet feminine and current.
Updates

Hi there, These are some artists websites that I Iike: Marnelvoss.com (I like how airy it is) peterwallombry.com garethpolvens.com (I like how it scrolls) I'll need a place for a photo ( a headshot-i do not have it yet so I'll need to be able to upload that later) as well as an area for my bio. Also, it's important that I will be able to upload any new photos and descriptions easily so it should be user friendly. Lastly, I like in a sunny place so would like to have this seem upbeat and playful as that is how i like to paint. thanks-I'm trying to upload my photos now -

Target Market(s)

ppl ages 35-70 who want large scale art for their homes

Industry/Entity Type

art

Coding

Coded - Design and coding required

Number of Pages Required

3 page

Colors

Designer to choose colors to be used in the design.

Requirements
Must have
• photos of my art, a place for my bio, be easy to reach me. tasteful-nothing too "in your face" -my clients are pretty high end and organized. They like clean lines
Nice to have
• sophisticated background, muted tones in the back-similar clean font throughout-no cursive
Should not have
• too many dark areas. Too many blocks of color. Too serious.

```html
<!DOCTYPE html>
<html lang="en">
<head>
<meta charset="utf-8">
<title>Helena Marsh Art – Contact</title>
<link href="https://fonts.googleapis.com/css2?family=Playfair+Display:wght@600&family=Poppins:wght@400;500;600&family=Tinos&display=swap" rel="stylesheet">
<style>
  :root {
    --ink: #111111;
    --nav-muted: #666666;
    --label: #444444;
    --rule: #d2d2d2;
    --field-line: #9a9a9a;
    --accent: #2f8ec9;
    --footer-bg: #f7f7f8;
    --white: #ffffff;
    --hero-start: #8795b1;
    --hero-mid: #3f8f93;
    --hero-end: #26406f;
  }
  * { box-sizing: border-box; margin: 0; padding: 0; }
  html, body { width: 1135px; height: 1200px; overflow: hidden; background: var(--white); }
  body { position: relative; font-family: "Poppins", sans-serif; color: var(--ink); }

  .site-title {
    position: absolute; top: 12px; left: 0; width: 100%;
    text-align: center; font-family: "Playfair Display", serif;
    font-weight: 600; font-size: 34px; line-height: 42px; letter-spacing: -0.3px;
  }
  .header-rule { position: absolute; top: 62px; left: 0; width: 100%; height: 1px; background: var(--rule); }

  .main-nav a {
    position: absolute; top: 81px; font-size: 16px; line-height: 22px;
    color: var(--nav-muted); text-decoration: none; text-transform: uppercase;
  }
  .main-nav a.is-active { color: var(--ink); font-weight: 500; }

  .hero-artwork {
    position: absolute; left: 94px; top: 126px; width: 947px; height: 337px;
    background: linear-gradient(90deg, var(--hero-start) 0%, var(--hero-mid) 50%, var(--hero-end) 100%);
  }

  .contact-heading {
    position: absolute; top: 500px; left: 0; width: 100%; text-align: center;
    font-weight: 400; font-size: 40px; line-height: 52px;
  }
  .contact-intro {
    position: absolute; top: 552px; left: 280px; width: 575px; text-align: center;
    font-size: 14.5px; line-height: 24.5px;
  }

  .field-label { position: absolute; font-size: 13.5px; line-height: 18px; color: var(--label); }
  .field-line { position: absolute; height: 1px; background: var(--field-line); }

  .submit-button {
    position: absolute; left: 506px; top: 956px; width: 123px; height: 43px;
    background: var(--accent); color: var(--white); border: 0;
    font-family: "Poppins", sans-serif; font-weight: 600; font-size: 14px; letter-spacing: 0.3px;
  }

  .site-footer { position: absolute; left: 0; top: 1061px; width: 100%; height: 139px; background: var(--footer-bg); }
  .social-links {
    position: absolute; top: 43px; left: 0; width: 100%;
    display: flex; justify-content: center; gap: 18px;
  }
  .social-item { display: flex; align-items: center; gap: 6px; font-size: 12px; line-height: 26px; color: var(--ink); }
  .social-dot { width: 26px; height: 26px; border: 1.2px solid var(--ink); border-radius: 50%; }
  .copyright {
    position: absolute; top: 93px; left: 0; width: 100%; text-align: center;
    font-family: "Tinos", serif; font-size: 14.5px; color: var(--ink);
  }
</style>
</head>
<body>
  <header>
    <div class="site-title">Helena Marsh Art</div>
    <div class="header-rule"></div>
    <nav class="main-nav">
      <a class="is-active" href="#" style="left:273px">Home</a>
      <a href="#" style="left:411px">About Me</a>
      <a href="#" style="left:583px">My Paintings</a>
      <a href="#" style="left:785px">Contact</a>
    </nav>
  </header>

  <div class="hero-artwork" role="img" aria-label="Featured abstract painting by the artist"></div>

  <main>
    <h1 class="contact-heading">Contact</h1>
    <p class="contact-intro">Sed ut perspiciatis unde omnis iste natus error sit voluptatem accusantium doloremque laudantium, totam rem aperiam, eaque ipsa</p>

    <form>
      <label class="field-label" style="left:146px;top:635px">First Name*</label>
      <div class="field-line" style="left:148px;top:685px;width:401px"></div>
      <label class="field-label" style="left:590px;top:635px">Last Name*</label>
      <div class="field-line" style="left:591px;top:685px;width:402px"></div>

      <label class="field-label" style="left:146px;top:736px">Email Address*</label>
      <div class="field-line" style="left:148px;top:786px;width:401px"></div>
      <label class="field-label" style="left:590px;top:736px">Phone Number*</label>
      <div class="field-line" style="left:591px;top:786px;width:402px"></div>

      <label class="field-label" style="left:146px;top:835px">Message*</label>
      <div class="field-line" style="left:148px;top:926px;width:851px"></div>

      <button class="submit-button" type="button">SUBMIT</button>
    </form>
  </main>

  <footer class="site-footer">
    <div class="social-links">
      <span class="social-item"><span class="social-dot"></span>Facefolio</span>
      <span class="social-item"><span class="social-dot"></span>Chirpline</span>
      <span class="social-item"><span class="social-dot"></span>Snapgallery</span>
    </div>
    <p class="copyright">©Copyright ©2022 Helena Marsh Art. All Rights Reserved.</p>
  </footer>
</body>
</html>
```